Business Card Re-Design...or logo does not look sharp

Hello

We are a start-up and just need someone to help us.

Our colors are: Rosalind charm pink (yeah I know) and charcoal for the lettering.

I am attaching our logo which needs cleaning up.

We want the JUST the lady ironing on the table (pink) in front, and the background in charcoal. All the business info can be on the back.

Dims on card are 2 x 2''

Also, if you have better ideas....please let us know!

Thanks

Gregory

Industry/Entity Type

Business

Contact Information for Business Card

Su Vecina Lavanda
4827 Bellcrest Ln Suite K2
El Paso TX 79912
915-555-0147

```html
<!DOCTYPE html>
<html lang="en">
<head>
<meta charset="utf-8">
<title>Su Vecina Lavanda — Business Card</title>
<link rel="stylesheet" href="https://fonts.googleapis.com/css2?family=Dancing+Script:wght@500&display=swap">
<style>
  :root {
    --backdrop: #ece8e3;
    --charcoal: #333331;
    --blush: #f6c9c0;
    --paper-white: #f4f2ef;
    --card-w: 490px;
    --card-h: 280px;
  }
  * { margin: 0; padding: 0; box-sizing: border-box; }
  html, body {
    width: 1200px;
    height: 797px;
    overflow: hidden;
    background: var(--backdrop);
  }
  .canvas {
    width: 1200px;
    height: 797px;
    display: flex;
    align-items: center;
    justify-content: center;
    gap: 80px;
  }
  .card {
    position: relative;
    width: var(--card-w);
    height: var(--card-h);
    background: var(--charcoal);
    overflow: hidden;
  }
  .card-back__details {
    position: absolute;
    top: 30px;
    right: 36px;
    text-align: right;
    color: var(--paper-white);
    font-family: "Dancing Script", cursive;
    font-weight: 500;
  }
  .card-back__name {
    font-size: 30px;
    line-height: 1.1;
    margin-bottom: 4px;
  }
  .card-back__line {
    font-size: 17px;
    line-height: 1.3;
  }
  .card-back__corner {
    position: absolute;
    left: 0;
    bottom: 0;
    width: 44px;
    height: 44px;
  }
  .card-front {
    display: flex;
    align-items: center;
    justify-content: center;
  }
  .card-front__name {
    color: var(--blush);
    font-family: "Dancing Script", cursive;
    font-weight: 500;
    font-size: 38px;
  }
</style>
</head>
<body>
<main class="canvas">
  <section class="card card-back" aria-label="Card back with business details">
    <div class="card-back__details">
      <p class="card-back__name">Su Vecina Lavanda</p>
      <p class="card-back__line">4827 Bellcrest Ln Suite K2</p>
      <p class="card-back__line">El Paso</p>
      <p class="card-back__line">TX 79912</p>
      <p class="card-back__line">915-555-0147</p>
    </div>
    <svg class="card-back__corner" viewBox="0 0 44 44" aria-hidden="true">
      <path d="M0 44 V10 Q0 0 10 0 Q34 0 44 44 Z" fill="var(--blush)"/>
    </svg>
  </section>

  <section class="card card-front" aria-label="Card front with business name">
    <p class="card-front__name">Su Vecina Lavanda</p>
  </section>
</main>
</body>
</html>
```